Flat bootstrap design for existing site

I'm looking for a modern flat design based around an existing logo. This has to be a custom design (no external templates), and implemented into a bootstrap framework.

The logo is attached as 2 versions - choose whichever you want, that flows better with whatever design you choose.

Added screenshots of the existing site (currently using the default bootstrap layouts). Please make your designs around those pages in the screenshots (i.e. the homepage only has the postal code input and the header). The active page has 3 screenshots, because I wanted to illustrate the other states that would be visible (in the table rows).

This is a moving/junk removal website, just for some context.

Here's some example websites (flat designs) that I like, just to give you an idea of what I'm after.

https://www.plimvora.com/
https://dacklow.com/
https://trevanu.com/
https://quobrintal.com/en/

Coding

Coded - Design and coding required

Number of Pages Required

5+ page

Colors

Designer to choose colors to be used in the design.

Requirements
Must have
• It must be a modern/simple flat design, that is built around the existing logo (attached).
• It has to be implemented using bootstrap.

```html
<!DOCTYPE html>
<html lang="en">
<head>
<meta charset="utf-8">
<title>Haulvex – Sign In</title>
<link rel="stylesheet" href="https://fonts.googleapis.com/css2?family=Mulish:wght@400;600;700;800&display=swap">
<style>
  :root {
    --sky-top: #22b4e9;
    --sky-bottom: #4ac9f5;
    --white: #ffffff;
    --placeholder: #8a8a8a;
    --footer-bg: #e9e9e9;
    --footer-text: #6f6f6f;
    --field-shadow: rgba(0, 60, 100, 0.18);
  }
  * { box-sizing: border-box; margin: 0; padding: 0; }
  html, body { width: 1200px; height: 732px; overflow: hidden; }
  body {
    font-family: "Mulish", sans-serif;
    position: relative;
    background: var(--footer-bg);
  }
  .hero {
    position: absolute; left: 0; top: 0;
    width: 1200px; height: 665px;
    background: linear-gradient(160deg, var(--sky-top) 0%, var(--sky-bottom) 100%);
    color: var(--white);
  }
  .brand {
    position: absolute; left: 156px; top: 36px;
    font-weight: 800; font-size: 44px; letter-spacing: 1px;
    color: var(--white); text-decoration: none; line-height: 1;
  }
  .main-nav {
    position: absolute; top: 46px; left: 0; width: 1200px; height: 30px;
  }
  .main-nav a {
    position: absolute; top: 0;
    color: var(--white); text-decoration: none;
    font-size: 17px; font-weight: 400; letter-spacing: 0.2px;
    line-height: 20px; white-space: nowrap;
  }
  .main-nav .nav-book { left: 532px; }
  .main-nav .nav-how { left: 617px; }
  .main-nav .nav-driver { left: 785px; }
  .main-nav .nav-signin { left: 974px; }
  .main-nav .is-active::after {
    content: ""; position: absolute; left: 1px; right: -2px; top: 29px;
    height: 2px; background: var(--white);
  }
  .signin-card {
    position: absolute; left: 382px; top: 211px;
    width: 442px; height: 313px;
    border: 2px solid var(--white); border-radius: 6px;
  }
  .signin-title {
    position: absolute; left: 0; top: 34px; width: 100%;
    text-align: center; font-size: 34px; font-weight: 800; line-height: 1.2;
  }
  .field {
    position: absolute; left: 40px; width: 360px; height: 46px;
    border: none; background: var(--white);
    box-shadow: 0 4px 10px var(--field-shadow);
    font-family: inherit; font-size: 17px; padding: 0 13px; color: #333;
  }
  .field::placeholder { color: var(--placeholder); }
  .field-email { top: 94px; }
  .field-password { top: 153px; }
  .btn-book {
    position: absolute; left: 128px; top: 227px;
    width: 184px; height: 56px;
    border: 2.5px solid var(--white); border-radius: 28px;
    background: transparent; color: var(--white);
    font-family: inherit; font-size: 21px; font-weight: 600;
  }
  .site-footer {
    position: absolute; left: 0; top: 665px; width: 1200px; height: 67px;
    background: var(--footer-bg);
    text-align: center; font-size: 13px; color: var(--footer-text);
    padding-top: 24px; padding-right: 12px;
  }
  .site-footer span { margin: 0 2px; }
</style>
</head>
<body>
  <header class="hero">
    <a class="brand" href="#">HAULVEX</a>
    <nav class="main-nav">
      <a class="nav-book" href="#">BOOK</a>
      <a class="nav-how" href="#">HOW IT WORKS</a>
      <a class="nav-driver is-active" href="#">BECOME A DRIVER</a>
      <a class="nav-signin" href="#">SIGN IN</a>
    </nav>
    <form class="signin-card">
      <h1 class="signin-title">Please Sign In</h1>
      <input class="field field-email" type="email" placeholder="Email address">
      <input class="field field-password" type="password" placeholder="Password">
      <button class="btn-book" type="button">Book Now</button>
    </form>
  </header>
  <footer class="site-footer">
    <span>© 2017 Company Name</span> <span>All right reserved</span> <span>Term of Use</span>
  </footer>
</body>
</html>
```